Residential Remodeling Contractor needs updated business card

I need a new design for my business card.
Name of the company is Ridgefell Construction. I need a card that commands presence, strength, integrity. I have been in business for 28 years. I am a Residential Remodeling Contractor that covers all aspects of a residential remodel and build.

```html
<!DOCTYPE html>
<html lang="en">
<head>
<meta charset="UTF-8">
<title>Ridgefell Construction – Business Card</title>
<link href="https://fonts.googleapis.com/css2?family=Montserrat:wght@400;600&display=swap" rel="stylesheet">
<style>
  :root {
    --backdrop: #b4b4b4;
    --card-navy: #233e7c;
    --ink-white: #ffffff;
    --ink-soft: #e3e8f4;
    --divider: rgba(255,255,255,0.55);
  }
  * { margin: 0; padding: 0; box-sizing: border-box; }
  html, body { width: 1200px; height: 900px; overflow: hidden; }
  body {
    background: var(--backdrop);
    position: relative;
    font-family: "Montserrat", sans-serif;
    color: var(--ink-white);
  }
  .card {
    position: absolute;
    width: 560px;
    height: 320px;
    background: var(--card-navy);
    box-shadow: 0 6px 18px rgba(0,0,0,0.25);
  }
  .card--front { left: 60px; top: 110px; }
  .card--back { left: 580px; top: 470px; }

  .wordmark {
    position: absolute;
    display: flex;
    align-items: center;
    gap: 16px;
  }
  .wordmark__square {
    background: var(--ink-white);
    flex: none;
  }
  .wordmark__name {
    font-family: "Montserrat", sans-serif;
    font-weight: 600;
    color: var(--ink-white);
    line-height: 1;
    white-space: nowrap;
  }

  .card--front .wordmark { left: 40px; top: 64px; }
  .card--front .wordmark__square { width: 40px; height: 40px; }
  .card--front .wordmark__name { font-size: 29px; }

  .card--back .wordmark { left: 70px; top: 138px; }
  .card--back .wordmark__square { width: 40px; height: 40px; }
  .card--back .wordmark__name { font-size: 29px; }

  .holder {
    position: absolute;
    left: 130px;
    top: 196px;
    width: 170px;
    text-align: right;
  }
  .holder__name { font-weight: 600; font-size: 21px; }
  .holder__role { font-size: 12px; color: var(--ink-soft); margin-top: 4px; }

  .divider {
    position: absolute;
    left: 318px;
    top: 184px;
    width: 1px;
    height: 74px;
    background: var(--divider);
  }

  .contacts {
    position: absolute;
    left: 336px;
    top: 186px;
    list-style: none;
    font-size: 11.5px;
    color: var(--ink-soft);
  }
  .contacts li {
    display: flex;
    align-items: center;
    gap: 8px;
    height: 23px;
  }
  .contacts svg { width: 13px; height: 13px; flex: none; }

  .address {
    position: absolute;
    left: 0;
    right: 0;
    bottom: 26px;
    text-align: center;
    font-size: 11.5px;
    color: var(--ink-soft);
    letter-spacing: 0.02em;
  }
</style>
</head>
<body>

<section class="card card--front" aria-label="Business card front">
  <div class="wordmark">
    <div class="wordmark__square"></div>
    <h1 class="wordmark__name">Ridgefell Construction</h1>
  </div>

  <div class="holder">
    <p class="holder__name">Daniel Marsh</p>
    <p class="holder__role">Owner</p>
  </div>

  <div class="divider"></div>

  <ul class="contacts">
    <li>
      <svg viewBox="0 0 16 16" aria-hidden="true"><path fill="#fff" d="M3.5 1.5l2.5 0 1 3.5-1.6 1.2a9 9 0 0 0 4.4 4.4L11 9l3.5 1v2.5c0 1-1 2-2 2A11 11 0 0 1 1.5 3.5c0-1 1-2 2-2z"/></svg>
      555.204.7730
    </li>
    <li>
      <svg viewBox="0 0 16 16" aria-hidden="true"><rect x="1" y="3" width="14" height="10" fill="#fff"/><path d="M1 3l7 6 7-6" fill="none" stroke="#233e7c" stroke-width="1.3"/></svg>
      info@ridgefellconstruction.com
    </li>
    <li>
      <svg viewBox="0 0 16 16" aria-hidden="true"><circle cx="8" cy="8" r="6.5" fill="none" stroke="#fff" stroke-width="1.4"/><ellipse cx="8" cy="8" rx="2.8" ry="6.5" fill="none" stroke="#fff" stroke-width="1.2"/><path d="M1.5 8h13" stroke="#fff" stroke-width="1.2"/></svg>
      www.ridgefellconstruction.com
    </li>
  </ul>

  <p class="address">240 Cedar Hollow Road Brandon, MS 39047</p>
</section>

<section class="card card--back" aria-label="Business card back">
  <div class="wordmark">
    <div class="wordmark__square"></div>
    <h2 class="wordmark__name">Ridgefell Construction</h2>
  </div>
</section>

</body>
</html>
```